4D Cradle Glimpse Luxury Ultrasound Billboard

Design a HIGH-END, MODERN billboard for my private prenatal ultrasound studio, 4D Cradle Glimpse, located in Pace, Florida.
This billboard will be viewed by drivers traveling at highway speeds, so it must be extremely clean, simple, and readable within 6 seconds.
About My Business
4D Cradle Glimpse is a private prenatal ultrasound studio specializing in:
Highest technology 4D/HD Ultrasounds
Early Gender Determination
Pregnancy Confirmation
I have been serving families for nearly 10 years and is known for creating a memorable experience, not just an ultrasound appointment.
Design Style
I DO NOT want:
Flowers
Leaves
Swirls
Glitter
Hearts everywhere
Busy backgrounds
Generic maternity stock graphics
I DO want:
Modern
Luxury
Upscale
Clean
Professional
Eye-catching
Premium medical spa feel
Colors
Use colors from my logo:
LOGO Green ( or a deep green)
Black
White
Soft Gold accents
Images:
Incorporate my professional headshot in a clean, modern way, logo, and the ultrasound images
Text
Keep wording minimal.
Primary Headline ( OPEN TO IDEAS) :
EXAMPLES ( WOULD RATHER SOMETHING MORE CATCHY)
" ADVANCED IMAGING. UNFORGETTABLE MOMENTS"
"MEET YOUR BABY BEFORE BIRTH"
Under headline:
4D Ultrasound • Early Gender • Pregnancy Confirmation
Business Name:
4D Cradle Glimpse
Private Prenatal Ultrasound Studio
Phone Number:
850-471-5923
Important
This billboard must be readable in 5–6 seconds from a moving vehicle.
Less text is better.
The phone number and business name must be visible from a distance.
The design should feel like a premium brand that immediately tells expecting parents:
“This is where I go to see my baby.”
Files Provided
Official logo
Headshot
Ultrasound images
Don’t make this look like a medical office billboard.
Make it look like a luxury baby experience billboard. That’s what separates 4D Cradle Glimpse from hospitals, OB offices, and all the new studios popping up around you. The emotional connection is what gets moms to book. ❤️
Billboard Size - 10.6” x 36”

```html
<!DOCTYPE html>
<html lang="en">
<head>
<meta charset="UTF-8">
<title>4D Cradle Glimpse Billboard</title>
<link href="https://fonts.googleapis.com/css2?family=Oswald:wght@600&family=Roboto+Condensed:wght@500;700&family=Roboto:wght@900&family=Great+Vibes&display=swap" rel="stylesheet">
<style>
  :root {
    --page: #f4f4f2;
    --ink: #070707;
    --gold: #c9a44a;
    --gold-light: #ecd27a;
    --gold-deep: #a9822e;
    --sage: #7d9185;
    --sage-light: #9aaea2;
    --white: #ffffff;
    --skin: #c98f6e;
  }
  * { margin: 0; padding: 0; box-sizing: border-box; }
  html, body { width: 1001px; height: 1200px; overflow: hidden; background: var(--page); }
  .billboard {
    position: absolute; left: 20px; top: 460px; width: 961px; height: 280px;
    background:
      radial-gradient(ellipse 180px 160px at 0% 0%, rgba(201,164,74,.75), transparent 70%),
      radial-gradient(ellipse 260px 220px at 100% 100%, rgba(120,70,20,.7), transparent 70%),
      radial-gradient(ellipse 220px 160px at 95% 0%, rgba(110,60,15,.55), transparent 70%),
      var(--ink);
    overflow: hidden;
    box-shadow: 0 18px 28px rgba(0,0,0,.25);
  }
  .brand-tag {
    position: absolute; left: 65px; top: 0; width: 120px; height: 82px;
    background: var(--white); border-radius: 0 0 8px 8px;
    display: flex; flex-direction: column; align-items: center; justify-content: center; gap: 4px;
    font-family: "Roboto Condensed", sans-serif; font-weight: 700; color: var(--gold-deep);
    text-align: center; font-size: 15px; line-height: 1.05;
  }
  .brand-tag .dot { width: 8px; height: 8px; border-radius: 50%; background: var(--sage); }
  .headshot {
    position: absolute; left: 36px; top: 91px; width: 157px; height: 189px;
    background: linear-gradient(180deg, #d9b97e 0%, #c89a78 45%, #2f4a33 100%);
    border-radius: 70px 70px 0 0; opacity: .95;
  }
  .studio-label {
    position: absolute; left: 174px; top: 157px; width: 125px; height: 98px;
    background: var(--sage); border-radius: 0 10px 10px 0;
    padding: 14px 0 0 34px;
    font-family: "Roboto Condensed", sans-serif; font-weight: 500; font-size: 15px;
    line-height: 17.5px; color: var(--white);
  }
  .headline { position: absolute; left: 300px; top: 0; width: 362px; height: 210px; font-weight: normal; }
  .headline .script {
    position: absolute; left: 100px; top: 10px;
    font-family: "Great Vibes", cursive; color: var(--white);
    font-size: 80px; line-height: 80px; z-index: 2;
  }
  .headline .main {
    position: absolute; left: 0; width: 362px; text-align: center;
    font-family: "Oswald", sans-serif; font-weight: 600;
    background: linear-gradient(180deg, var(--gold-light), var(--gold) 55%, var(--gold-deep));
    -webkit-background-clip: text; background-clip: text; color: transparent;
    font-size: 58px; line-height: 62px; letter-spacing: -1px;
  }
  .headline .line-one { top: 80px; }
  .headline .line-two { top: 142px; }
  .services {
    position: absolute; left: 322px; top: 223px; display: flex; align-items: center;
    font-family: "Roboto Condensed", sans-serif; font-weight: 500; font-size: 14px;
    line-height: 16px; color: var(--white);
  }
  .service { display: flex; align-items: flex-start; gap: 6px; padding: 0 11px; }
  .service + .service { border-left: 1.5px solid var(--white); }
  .service svg { width: 18px; height: 18px; flex: none; }
  .keepsake-photo {
    position: absolute; left: 676px; top: 39px; width: 285px; height: 181px;
    background: radial-gradient(ellipse at 45% 45%, var(--skin), #8a5a3e 55%, transparent 80%);
  }
  .phone-bar {
    position: absolute; left: 662px; top: 218px; width: 299px; height: 37px;
    background: linear-gradient(90deg, var(--sage), var(--sage-light));
    border-radius: 18px 0 0 18px; display: flex; align-items: center; gap: 20px; padding-left: 10px;
    font-family: "Roboto", sans-serif; font-weight: 900; font-size: 27px;
    letter-spacing: 1.5px; color: var(--white);
  }
  .phone-bar .icon { width: 20px; height: 20px; border-radius: 50%; background: var(--gold); display: flex; align-items: center; justify-content: center; flex: none; }
</style>
</head>
<body>
  <section class="billboard">
    <div class="headshot" role="img" aria-label="Professional headshot of the studio owner"></div>
    <div class="brand-tag"><span>4D Cradle<br>Glimpse</span><span class="dot"></span></div>
    <div class="studio-label">Private<br>Prenatal<br>Ultrasound<br>Studio</div>

    <div class="keepsake-photo" role="img" aria-label="Family hands holding an ultrasound print of twin babies"></div>

    <h1 class="headline">
      <span class="main line-one">YOUR BABY</span>
      <span class="main line-two">BEFORE BIRTH</span>
      <span class="script">Meet</span>
    </h1>

    <div class="services">
      <div class="service">
        <svg viewBox="0 0 18 18"><rect x="1" y="2" width="13" height="9" rx="1" fill="none" stroke="#c9a44a" stroke-width="2"/><path d="M5 14h6M8 11v3M15 6v8" stroke="#c9a44a" stroke-width="2"/></svg>
        <span>4D<br>Ultrasound</span>
      </div>
      <div class="service">
        <svg viewBox="0 0 18 18"><circle cx="5" cy="9" r="3.5" fill="none" stroke="#c9a44a" stroke-width="1.6"/><path d="M7.5 6.5l3-3M8 3.5h2.5V6" fill="none" stroke="#c9a44a" stroke-width="1.6"/><circle cx="13" cy="7" r="3.5" fill="none" stroke="#c9a44a" stroke-width="1.6"/><path d="M13 10.5v6M10.5 14h5" stroke="#c9a44a" stroke-width="1.6"/></svg>
        <span>Early<br>Gender</span>
      </div>
      <div class="service">
        <svg viewBox="0 0 18 18"><path d="M3 15L14 4l1.5 1.5L4.5 16.5z" fill="#c9a44a"/><path d="M13 2l3 3" stroke="#c9a44a" stroke-width="2"/></svg>
        <span>Pregnancy<br>Confirmation</span>
      </div>
    </div>

    <div class="phone-bar">
      <span class="icon"><svg width="12" height="12" viewBox="0 0 24 24"><path d="M6.6 10.8a15 15 0 006.6 6.6l2.2-2.2a1 1 0 011-.25 11.4 11.4 0 003.6.6 1 1 0 011 1V20a1 1 0 01-1 1A17 17 0 013 4a1 1 0 011-1h3.5a1 1 0 011 1c0 1.25.2 2.45.6 3.6a1 1 0 01-.25 1z" fill="#fff"/></svg></span>
      850-471-5923
    </div>
  </section>
</body>
</html>
```